Snapnook needs You

Help us create an inviting, amazing, sleek, simple, clear landing page for a picture-memory-social connection site!

Business Name: SnapNook
Industry: Social Networking and Creativity through Pictures
A web platform for and about a community that is driven by a passion for sharing, caring, bonding, collaborating, creating and earning with pictures, through pictures and other related creative activities. This is going to be a great site for all creative artists-photographers, artists, graphic artists to express their work and their creativity.

The main focus of the site is - CONNECTIONS.
This will be uncoded.

Desired Website Screen Size
1024x768... Widescreen/Landscape orientation, is what we mean... So it fits on a CPU screen.

Desired look and feel and message
Look: Visitor should feel immersed in the page, in the world the page creates, simple, elegant, sophisticated, contemporary. We really like a clean uncluttered look.

Special mention: By the way we love the marketing genius who thought up this branding for velu yogurt where they used the two dots above the o to create a branding effect that made this brand instantly identifiable. http://www.velu-dairy.ca/en/

The two dots by themselves without having even the name present brings up the whole brand now. The dots are used above all the ingredients of the yogurt creating friendly figures, and above people in commercials-bringing the people onto the side of "team" velu. Snapnook may have a character created or something distinctive in the letters in the name created to brand the site as well.

Feel: Engaging; Magical without being corny, here is a link to give an example look and feel but please do not be hindered in your creativity by this suggestion. We love all creative angles.
http://artscrapyard.com/graphic/5829317-camera-film-roll-blue-background

Message: Life and memories and connections through pictures.

Target audience:
The site is focused on pictures but not confined to photography enthusiasts (although they are an integral part of the site). Customers/Visitors will include families, corporates and the younger generation - all age groups, all class, everyone with pictures to express, memories to share.

Website design we like:
http://brindlework.com/work/northern-ballet-house/
http://brindlework.com/work/zapverse/

What colors do we want to see on our landing page?
We would like the background to be grey or blue since it is grey is picture neutral colour and blue highlights pictures well and we also like blue and silver, which can be integrated into the theme. Also like green. But please do not let these instructions limit your creativity. We are open to new ideas and colours.

Predetermined Concepts if any:
We have a concept in mind and we think it would be cool to have an interface for the user through the back of a camera on the landing page -This could be used to create a scene or world the visitor feels a part of or is immersed into. The back screen of the camera may act as a screen for the slideshow of featured pictures on the site.

Content on the Page:
Photo Gallery with full screen, thumbnail view, zoom option etc.
Prominent but short introductory message
Sign in / Login Options
Links: Home Page; About; Info/Help; Contact Us; Privacy Policy; Terms of Use
At the bottom of the page: Follow Me/Like/Workplaza...social buttons.

Please feel free to add any other element to the landing page that you think might add to the effect of simple yet amazing look -clean, simple, uncluttered, sophisticated, stylish, inviting and engaging.
The concept is a guideline, but we would like you to be as creative as you can, even if it meant stepping out of these guidelines - rethink design, style, content if you like. We believe in bringing a solution in an innovative yet simple and elegant style. Something a visitor would be intrigued enough to explore and the guest would feel comfortable enough taking that step forward to have fun on the site. If you believe in the same, and you have the skill then you will have what we need. Good luck, go for it and we are excited to see what the amazing designers on this amazing site have to offer.
If you have any questions please free to ask.

HI wanted to send an update that this project design has been guaranteed.

Our site will be one to celebrate and showcase imagination as well as connection.  We would love to see what you create. Keep in mind our site will showcase all creativity, photographs, artists, graphic artists so this would be a benefit you may want to take advantage of in the future, a place where, if you so choose, you could gain exposure for your work. Therefore, even if you do not win the design project there is possible future benefit.

Imagination is everything.
Imagination encircles the world.-Halvorsen

Reason: We are giving the designers who accepted invites but have not yet submitted a chance to finish their submissions and the ones who are working on revisions a chance to finish those:)

Hello everyone,

Due to time constraints we must come to a decision sooner than the deadline of 28th. 

So, please try to submit any new designs or modifications to the old ones before the 26th. We are very thankful to all of you who have participated - for your designs, enthusiasm and kind words. 

Good luck! :)

• Thank you for the interest shown and your submissions! Designers who have submitted up until now have shown great potential. We are VERY excited with the quality of work and designs.

We want to add that Snapnook is not exclusively for the photographers. The site is for every person who may have a picture to store, organise, use or share - whether publicly or with only a few friends and family.

Snapnook is about allowing people to take control of their creativity. It is about providing tools to our users so that they can build their own connections and social network... of friends, family, fans, clients, ideas, thoughts, emotions etc. through pictures without worrying about their privacy or control over their creations.

With this update we want to encourage others to go beyond the camera theme. Do not let us restrict your creativity. Let YOUR OWN ideas take over if that’s what you think will best convey the message and will appeal to the users.

```html
<!DOCTYPE html>
<html lang="en">
<head>
<meta charset="utf-8">
<title>SnapNook – Professional Photo</title>
<link rel="stylesheet" href="https://fonts.googleapis.com/css2?family=Arimo:ital,wght@0,400;0,700;1,400;1,700&display=swap">
<style>
  :root {
    --ink-black: #050505;
    --camera-grey: #5a5a5a;
    --white: #ffffff;
    --band-white: #f4f4f4;
    --navy: #0d2a78;
    --navy-deep: #0a1f5c;
    --text-grey: #4a4a4a;
    --cyan: #14cbf2;
    --cyan-light: #4fdcfa;
    --cyan-dark: #0fb6dc;
    --footer-grey: #3c3c3c;
    --arrow-yellow: #f5b800;
    --icon-grey: #9a9a9a;
  }
  * { margin: 0; padding: 0; box-sizing: border-box; }
  html, body { width: 1200px; height: 675px; overflow: hidden; background: var(--ink-black); }
  body { font-family: "Arimo", Arial, sans-serif; }
  .page { position: relative; width: 1200px; height: 675px; overflow: hidden; }

  .hero-backdrop {
    position: absolute; left: 0; top: 0; width: 1200px; height: 484px;
    background:
      radial-gradient(ellipse 520px 360px at 560px 300px, #7a7a7a 0%, #4a4a4a 45%, #1c1c1c 80%, var(--ink-black) 100%);
  }

  .brand { position: absolute; left: 186px; top: 48px; color: var(--white); font-size: 29px; letter-spacing: 0.5px; }
  .tagline { position: absolute; left: 361px; top: 59px; color: var(--white); font-size: 12px; font-style: italic; }

  .social { position: absolute; left: 684px; top: 59px; display: flex; gap: 1px; }
  .social span { width: 17px; height: 17px; background: var(--icon-grey); display: block; }

  .search-icon { position: absolute; left: 766px; top: 59px; }
  .search-box {
    position: absolute; left: 793px; top: 55px; width: 183px; height: 22px;
    background: var(--white); border-radius: 4px; padding-left: 8px;
    color: var(--navy); font-size: 14px; font-style: italic; line-height: 22px;
  }

  .slide { position: absolute; }
  .slide--prev { left: 0; top: 178px; width: 258px; height: 214px;
    background: linear-gradient(135deg, #6b5a2a 0%, #4a3018 50%, #2a1c10 100%); }
  .slide--main { left: 336px; top: 145px; width: 506px; height: 270px;
    background: linear-gradient(160deg, #6fa2d8 0%, #c8dcef 40%, #eef4fa 70%, #9fb8cf 100%); }
  .slide--next { left: 916px; top: 175px; width: 284px; height: 208px;
    background: linear-gradient(170deg, #8e98a2 0%, #4b5866 45%, #1f2c3a 100%); }
  .arrow { position: absolute; }
  .arrow--prev { left: 287px; top: 258px; }
  .arrow--next { left: 870px; top: 254px; }

  .intro-band {
    position: absolute; left: 0; top: 484px; width: 1200px; height: 103px;
    background: linear-gradient(180deg, var(--white) 0%, var(--band-white) 60%, #e4e4e4 100%);
    border-top: 1px solid #9a9a9a;
  }
  .free-trial { position: absolute; left: 263px; top: 512px; color: var(--navy); font-size: 14px; font-style: italic; word-spacing: 4px; }
  .signup-btn {
    position: absolute; left: 355px; top: 509px; width: 80px; height: 21px;
    background: linear-gradient(180deg, #1a3c96, var(--navy-deep)); border-radius: 3px;
    color: var(--white); font-size: 14px; font-style: italic; text-align: center; line-height: 21px;
  }
  .intro-text { position: absolute; left: 556px; top: 513px; width: 430px; color: var(--text-grey); font-size: 11.6px; font-style: italic; line-height: 12.5px; }

  .nav-band { position: absolute; left: 0; top: 587px; width: 1200px; height: 37px; background: var(--cyan); }
  .nav-tabs { position: absolute; left: 0; top: 0; }
  .nav-link { position: absolute; top: 9px; color: var(--white); font-size: 16px; }
  .sign-in-label { position: absolute; left: 745px; top: 8px; color: var(--white); font-size: 19px; font-style: italic; }
  .sign-in-field { position: absolute; left: 826px; top: 9px; width: 156px; height: 23px; background: var(--white); border-radius: 4px; border: 1px solid #bfeefb; }

  .footer { position: absolute; left: 0; top: 624px; width: 1200px; height: 51px; background: linear-gradient(180deg, #444, var(--footer-grey)); }
  .footer-line { position: absolute; left: 0; top: 15px; width: 1200px; text-align: center; color: #e2e2e2; font-size: 10px; font-style: italic; }
  .footer-brand { font-size: 14px; font-style: normal; color: var(--white); margin: 0 8px; }
</style>
</head>
<body>
<div class="page">
  <div class="hero-backdrop" role="img" aria-label="Blurred close-up of the back of a black professional camera"></div>

  <div class="brand">SNAPNOOK</div>
  <div class="tagline">PROFESHIONAL PHTO</div>

  <div class="social" aria-label="Social links"><span></span><span></span><span></span><span></span></div>

  <svg class="search-icon" width="20" height="20" viewBox="0 0 20 20" aria-hidden="true">
    <circle cx="12" cy="7" r="5" fill="none" stroke="#fff" stroke-width="2.4"/>
    <line x1="8.5" y1="10.5" x2="2.5" y2="17" stroke="#fff" stroke-width="3" stroke-linecap="round"/>
  </svg>
  <div class="search-box">Search</div>

  <div class="slide slide--prev" role="img" aria-label="Close-up of a chestnut in its spiky husk"></div>
  <div class="slide slide--main" role="img" aria-label="Skier descending a snowy mountain slope above a glacial valley"></div>
  <div class="slide slide--next" role="img" aria-label="Orca surfacing by the edge of an ice shelf"></div>

  <svg class="arrow arrow--prev" width="20" height="22" viewBox="0 0 20 22" aria-label="Previous">
    <polygon points="11,0 19,0 9,11 19,22 11,22 1,11" fill="var(--arrow-yellow)"/>
  </svg>
  <svg class="arrow arrow--next" width="20" height="22" viewBox="0 0 20 22" aria-label="Next">
    <polygon points="1,0 9,0 19,11 9,22 1,22 11,11" fill="var(--arrow-yellow)"/>
  </svg>

  <div class="intro-band"></div>
  <div class="free-trial">FREE TRIAL</div>
  <div class="signup-btn">SIGN UP</div>
  <p class="intro-text">Te dicam labitur mel, est eu graeco minimum, in sit facer assueverit inciderint. Laudem diceret no his, et mea minim nominati democritum, at quo partem numquam feugiat. Liber primis maiestatis ius ut. Ius liber congue laboramus ne.</p>

  <nav class="nav-band">
    <svg class="nav-tabs" width="600" height="37" viewBox="0 0 600 37" aria-hidden="true">
      <polygon points="210,0 304,0 298,37 204,37" fill="var(--cyan-light)"/>
      <polygon points="307,0 399,0 393,37 301,37" fill="var(--cyan-dark)"/>
      <polygon points="402,0 484,0 478,37 396,37" fill="var(--cyan-dark)"/>
      <polygon points="487,0 567,0 561,37 481,37" fill="var(--cyan-dark)"/>
    </svg>
    <span class="nav-link" style="left:230px">home</span>
    <span class="nav-link" style="left:315px">products</span>
    <span class="nav-link" style="left:415px">about</span>
    <span class="nav-link" style="left:500px">contact</span>
    <span class="sign-in-label">SIGN IN</span>
    <div class="sign-in-field"></div>
  </nav>

  <footer class="footer">
    <div class="footer-line">minimum, in sit facer assueverit inciderint.<span class="footer-brand">SNAPNOOK</span>minimum, in sit facer assueverit inciderint.</div>
  </footer>
</div>
</body>
</html>
```